Professional, Attractive, Simple Website Needed!!

We completed the design for our logo.

We need a website built out around this.

Here are a couple samples of how we want ours formatted.

http://brimvoltco.com

http://www.ravelbeam.com/lp/free-quote?LeadSource=Search%20Engine&ProgramName=searchads&experience=qual&language=en&type=brd&gclid=Xk7PLmqwTRZBNVuEYcaHdFgWsLoPeRtQnMxVbCzJaKiOuYtReWqAsDfGhJkLzXcVbNmQwErTyUiOpAsDfGhJkLzX_wcB

http://quorel.co
Updates

Project Deadline Extended
Reason: Extending this deadline due to our delay in providing designers with content for each page. This is coming in next 24 hours.

Project Deadline Extended
Reason: Due to scheduling conflicts and extended travel delays related to Puerto Rico, the deadline has been extended. Your patience is greatly appreciated.

Project Deadline Extended
Reason: Travel and scheduling conflicts have made it impossible to give this project the thorough review it deserves, therefore I am extending the deadline. Thank you for your patience!

Target Market(s)

Home Owners who earn 60k + household annually

Industry/Entity Type

It Professional

Coding

Coded - Design and coding required

Number of Pages Required

5+ page

Font styles to use
Serif

Colors
34a7d8
9bcb3c

Requirements
Must have
• Simple
• Lead form Entry (Ability for visitor to enter Name, number and address for a quote)
• Sleek Design
• Professional
• Testimonials
• Use color Scheme of Design Logo Attached
Nice to have
• Video when site starts
• Like this
• https://www.vidplexa.com/watch?v=Qm8rTbLw3Np&feature=vidplexa.be
Should not have
• Should not include Commercial solar
• Should not include wind power

```html
<!DOCTYPE html>
<html lang="en">
<head>
<meta charset="utf-8">
<title>Sunvale Energy</title>
<link href="https://fonts.googleapis.com/css2?family=Montserrat:wght@400;600;700&family=Open+Sans:wght@400;600;700&display=swap" rel="stylesheet">
<style>
:root{
  --blue:#34a7d8;
  --blue-dark:#1f8fc2;
  --green:#9bcb3c;
  --green-dark:#86b52c;
  --ink:#333a40;
  --muted:#8a9096;
  --line:#e3e6e8;
  --soft:#f5f6f7;
  --star:#f2b632;
  --white:#ffffff;
}
*{box-sizing:border-box;margin:0;padding:0}
html,body{width:1200px;height:2488px;overflow:hidden}
body{font-family:"Open Sans",Arial,sans-serif;color:var(--ink);background:var(--white);position:relative}
h1,h2,h3,h4{font-family:"Montserrat",Arial,sans-serif}

/* header */
.site-header{position:absolute;top:0;left:0;width:1200px;height:104px;background:var(--white);display:flex;align-items:center;justify-content:space-between;padding:0 40px 0 70px;z-index:3}
.brand{display:flex;align-items:center;gap:12px}
.brand-dot{width:46px;height:46px;border-radius:50%;background:var(--blue);flex:none}
.brand-name{font-family:"Montserrat",sans-serif;font-weight:700;font-size:22px;color:var(--blue);white-space:nowrap}
.main-nav{display:flex;align-items:center;gap:6px}
.main-nav a{font-family:"Montserrat",sans-serif;font-size:12px;font-weight:600;color:var(--ink);text-decoration:none;padding:10px 16px;letter-spacing:.5px}
.main-nav a.active{background:var(--green);color:var(--white)}
.nav-search{width:34px;height:34px;border-radius:50%;border:2px solid var(--green);margin-left:10px;display:flex;align-items:center;justify-content:center}

/* hero */
.hero{position:absolute;top:104px;left:0;width:1200px;height:800px}
.hero-media{position:absolute;inset:0;background:linear-gradient(180deg,#6fa7d3 0%,#a9cbe4 30%,#e9e2c8 42%,#2f5d86 55%,#1e3f62 72%,#5a8a3a 100%)}
.hero-curve{position:absolute;left:0;bottom:-1px;width:1200px;height:120px}
.hero-title{position:absolute;top:52px;width:100%;text-align:center;color:var(--white);font-size:44px;font-weight:700;letter-spacing:2px}
.hero-sub{position:absolute;top:112px;width:100%;text-align:center;color:var(--white);font-size:17px;letter-spacing:1.5px;text-transform:uppercase}
.play-btn{position:absolute;top:172px;left:558px;width:84px;height:84px}

.quote-box{position:absolute;top:560px;left:432px;width:336px;height:330px;background:rgba(40,44,48,.88);padding:30px 34px;z-index:2}
.quote-box h3{color:var(--white);text-align:center;font-size:22px;font-weight:600;margin-bottom:24px}
.quote-box .field{display:block;width:100%;height:40px;background:var(--white);margin-bottom:14px;padding:0 12px;font-size:13px;color:var(--muted);line-height:40px}
.quote-box .submit{display:block;width:100%;height:42px;background:var(--green);color:var(--white);text-align:center;line-height:42px;font-family:"Montserrat",sans-serif;font-weight:600;font-size:13px;letter-spacing:1px;margin-top:8px}

/* section titles */
.section-title{text-align:center;color:var(--green);font-size:32px;font-weight:600;line-height:40px}
.section-lead{text-align:center;color:var(--muted);font-size:13px;line-height:21px;width:760px;margin:12px auto 0}

/* welcome / steps */
.welcome{position:absolute;top:950px;left:0;width:1200px}
.steps{position:relative;display:flex;justify-content:center;gap:110px;margin-top:44px}
.steps-line{position:absolute;top:75px;left:240px;width:720px;border-top:2px dashed var(--green)}
.step{width:190px;text-align:center;position:relative}
.step-circle{width:150px;height:150px;border-radius:50%;border:4px solid var(--green);background:var(--white);margin:0 auto;display:flex;align-items:center;justify-content:center;position:relative;z-index:1}
.step h4{font-size:16px;font-weight:700;margin-top:22px;line-height:21px}
.step p{font-size:12px;color:var(--muted);margin-top:10px;line-height:18px}

/* testimonials */
.testimonials{position:absolute;top:1380px;left:0;width:1200px;height:380px;background:var(--soft);padding-top:50px}
.testimonial-row{display:flex;justify-content:center;gap:50px;margin-top:40px}
.testimonial{width:320px;display:flex;gap:16px}
.avatar{width:70px;height:70px;border-radius:50%;background:linear-gradient(135deg,#c9a98a,#7a5a44);flex:none}
.quote-mark{font-family:Georgia,serif;color:var(--green);font-size:40px;line-height:28px;position:absolute;margin-left:-28px}
.testimonial-body{position:relative}
.testimonial-body p{font-size:12px;color:var(--muted);line-height:19px}
.testimonial-body .client-name{font-size:12px;font-weight:700;color:var(--green);margin-top:12px;text-transform:uppercase}
.testimonial-body .client-date{font-size:11px;color:var(--muted);margin-top:2px}
.testimonial-body .stars{color:var(--star);font-size:14px;letter-spacing:2px;margin-top:4px}

/* blog */
.blog{position:absolute;top:1800px;left:0;width:1200px}
.blog-row{display:flex;justify-content:center;gap:30px;margin-top:30px}
.post{width:340px}
.post-media{height:200px}
.post-media.a{background:linear-gradient(160deg,#8ec3e8,#2c5d92 60%,#1d3c63)}
.post-media.b{background:linear-gradient(180deg,#4a9ee0,#8cc6ee 45%,#2b4f78 70%,#2a5a2d)}
.post-media.c{background:linear-gradient(160deg,#cfe3f2,#b66b48 55%,#3b4b63)}
.post h4{font-size:16px;font-weight:600;margin-top:14px}
.post p{font-size:12px;color:var(--muted);line-height:19px;margin-top:8px}
.post-meta{display:flex;gap:22px;font-size:11px;color:var(--green);margin-top:10px}

/* footer */
.site-footer{position:absolute;top:2272px;left:0;width:1200px;height:216px;background:var(--blue);color:var(--white)}
.footer-cols{display:flex;padding:28px 60px 0 80px;gap:60px}
.footer-brand{width:200px;display:flex;align-items:center;gap:10px;padding-top:30px;align-self:flex-start}
.footer-brand .brand-dot{background:var(--white);width:40px;height:40px}
.footer-brand .brand-name{color:var(--white);font-size:20px}
.footer-col h4{font-size:14px;font-weight:700;letter-spacing:1px;margin-bottom:12px}
.footer-col p,.footer-col li{font-size:11px;line-height:18px;color:#e5f4fb;list-style:none}
.col-info{width:220px}
.col-contact{width:230px}
.col-contact li{display:flex;align-items:center;gap:8px;margin-bottom:4px}
.col-news{width:240px}
.news-form{display:flex;margin-top:10px}
.news-input{flex:1;height:32px;background:var(--white);color:var(--muted);font-size:11px;line-height:32px;padding-left:10px}
.news-btn{width:40px;height:32px;background:var(--green)}
.footer-bottom{position:absolute;bottom:16px;left:80px;right:60px;display:flex;justify-content:space-between;align-items:center;font-size:11px}
.social{display:flex;gap:8px}
.social span{width:28px;height:28px;border-radius:50%;border:1.5px solid var(--white)}
</style>
</head>
<body>

<header class="site-header">
  <div class="brand"><span class="brand-dot"></span><span class="brand-name">Sunvale Energy</span></div>
  <nav class="main-nav">
    <a class="active">HOME</a><a>ABOUT US</a><a>SERVICES</a><a>TESTIMONIALS</a><a>VIDEO</a><a>CONTACT US</a>
    <span class="nav-search"><svg width="14" height="14" viewBox="0 0 14 14"><circle cx="6" cy="6" r="4.5" fill="none" stroke="#9bcb3c" stroke-width="2"/><line x1="9.5" y1="9.5" x2="13" y2="13" stroke="#9bcb3c" stroke-width="2"/></svg></span>
  </nav>
</header>

<section class="hero">
  <div class="hero-media" role="img" aria-label="Rows of solar panels on green grass under a bright blue sky"></div>
  <h1 class="hero-title">SUNVALE ENERGY</h1>
  <p class="hero-sub">Sed ut perspiciatis unde omnis iste natus error sit voluptatem</p>
  <svg class="play-btn" viewBox="0 0 84 84"><circle cx="42" cy="42" r="39" fill="rgba(255,255,255,.15)" stroke="#fff" stroke-width="3"/><path d="M34 27 L60 42 L34 57 Z" fill="#fff"/></svg>
  <svg class="hero-curve" viewBox="0 0 1200 120" preserveAspectRatio="none"><path d="M0 120 L0 40 Q600 150 1200 40 L1200 120 Z" fill="#fff"/></svg>
</section>

<form class="quote-box">
  <h3>Request A Quote</h3>
  <span class="field">Name</span>
  <span class="field">Number</span>
  <span class="field">Address</span>
  <span class="submit">REQUEST A QUOTE</span>
</form>

<section class="welcome">
  <h2 class="section-title">Welcome to Sunvale Energy</h2>
  <p class="section-lead">Sed ut perspiciatis unde omnis iste natus error sit voluptatem accusantium doloremque laudantium, totam rem aperiam, eaque ipsa quae ab illo inventore veritatis et quasi architecto beatae vitae dicta sunt explicabo.</p>
  <div class="steps">
    <div class="steps-line"></div>
    <div class="step">
      <div class="step-circle"><svg width="64" height="54" viewBox="0 0 64 54"><rect x="2" y="6" width="60" height="40" rx="3" fill="none" stroke="#34a7d8" stroke-width="3"/><circle cx="20" cy="22" r="6" fill="#9bcb3c"/><path d="M10 40 Q20 28 30 40" fill="#9bcb3c"/><line x1="36" y1="18" x2="54" y2="18" stroke="#34a7d8" stroke-width="3"/><line x1="36" y1="27" x2="54" y2="27" stroke="#34a7d8" stroke-width="3"/></svg></div>
      <h4>Speak to a<br>solar consultant</h4>
      <p>Sed ut perspiciatis unde omnis iste natus error sit voluptatem</p>
    </div>
    <div class="step">
      <div class="step-circle"><svg width="64" height="54" viewBox="0 0 64 54"><path d="M10 6 H54 L62 40 H2 Z" fill="none" stroke="#34a7d8" stroke-width="3"/><line x1="6" y1="23" x2="58" y2="23" stroke="#34a7d8" stroke-width="2"/><line x1="25" y1="6" x2="22" y2="40" stroke="#34a7d8" stroke-width="2"/><line x1="39" y1="6" x2="42" y2="40" stroke="#34a7d8" stroke-width="2"/><line x1="32" y1="40" x2="32" y2="52" stroke="#9bcb3c" stroke-width="3"/></svg></div>
      <h4>We'll design your<br>solar panel system</h4>
      <p>Sed ut perspiciatis unde omnis iste natus error sit voluptatem</p>
    </div>
    <div class="step">
      <div class="step-circle"><svg width="56" height="56" viewBox="0 0 56 56"><rect x="3" y="8" width="50" height="44" rx="3" fill="none" stroke="#34a7d8" stroke-width="3"/><rect x="3" y="8" width="50" height="12" fill="#34a7d8"/><path d="M18 35 L25 42 L39 28" fill="none" stroke="#9bcb3c" stroke-width="4"/></svg></div>
      <h4>Schedule your<br>1 day install</h4>
      <p>Sed ut perspiciatis unde omnis iste natus error sit voluptatem</p>
    </div>
    <div class="step">
      <div class="step-circle"><svg width="56" height="56" viewBox="0 0 56 56"><circle cx="28" cy="28" r="25" fill="#9bcb3c"/><text x="28" y="38" text-anchor="middle" font-family="Montserrat,sans-serif" font-size="28" font-weight="700" fill="#fff">$</text></svg></div>
      <h4>Start saving on your<br>electricity bill</h4>
      <p>Sed ut perspiciatis unde omnis iste natus error sit voluptatem</p>
    </div>
  </div>
</section>

<section class="testimonials">
  <h2 class="section-title">Our Testimonials</h2>
  <p class="section-lead">Sed ut perspiciatis unde omnis iste natus error sit voluptatem accusantium doloremque laudantium, totam rem aperiam.</p>
  <div class="testimonial-row">
    <div class="testimonial">
      <div class="avatar" role="img" aria-label="Client portrait"></div>
      <div class="testimonial-body"><span class="quote-mark">&ldquo;</span>
        <p>Sed ut perspiciatis unde omnis iste natus error sit voluptatem accusantium doloremque laudantium, totam rem aperiam eaque.</p>
        <p class="client-name">Jane Smith</p><p class="client-date">Posted on 10 May 2017</p><p class="stars">★★★★★</p>
      </div>
    </div>
    <div class="testimonial">
      <div class="avatar" role="img" aria-label="Client portrait"></div>
      <div class="testimonial-body"><span class="quote-mark">&ldquo;</span>
        <p>Sed ut perspiciatis unde omnis iste natus error sit voluptatem accusantium doloremque laudantium, totam rem aperiam eaque.</p>
        <p class="client-name">John Carter</p><p class="client-date">Posted on 14 May 2017</p><p class="stars">★★★★★</p>
      </div>
    </div>
    <div class="testimonial">
      <div class="avatar" role="img" aria-label="Client portrait"></div>
      <div class="testimonial-body"><span class="quote-mark">&ldquo;</span>
        <p>Sed ut perspiciatis unde omnis iste natus error sit voluptatem accusantium doloremque laudantium, totam rem aperiam eaque.</p>
        <p class="client-name">Mark Ellis</p><p class="client-date">Posted on 21 May 2017</p><p class="stars">★★★★★</p>
      </div>
    </div>
  </div>
</section>

<section class="blog">
  <h2 class="section-title">Latest Blog</h2>
  <p class="section-lead">Sed ut perspiciatis unde omnis iste natus error sit voluptatem accusantium doloremque laudantium.</p>
  <div class="blog-row">
    <article class="post">
      <div class="post-media a" role="img" aria-label="Close view of blue solar panels"></div>
      <h4>Neque porro quisquam</h4>
      <p>Sed ut perspiciatis unde omnis iste natus error sit voluptatem accusantium doloremque laudantium, totam rem aperiam.</p>
      <div class="post-meta"><span>&#9679; 2 June 2017</span><span>&#9679; 12 Comments</span></div>
    </article>
    <article class="post">
      <div class="post-media b" role="img" aria-label="Solar panel array in a field under blue sky"></div>
      <h4>Neque porro quisquam</h4>
      <p>Sed ut perspiciatis unde omnis iste natus error sit voluptatem accusantium doloremque laudantium, totam rem aperiam.</p>
      <div class="post-meta"><span>&#9679; 5 June 2017</span><span>&#9679; 8 Comments</span></div>
    </article>
    <article class="post">
      <div class="post-media c" role="img" aria-label="Solar panels on a house roof"></div>
      <h4>Neque porro quisquam</h4>
      <p>Sed ut perspiciatis unde omnis iste natus error sit voluptatem accusantium doloremque laudantium, totam rem aperiam.</p>
      <div class="post-meta"><span>&#9679; 9 June 2017</span><span>&#9679; 15 Comments</span></div>
    </article>
  </div>
</section>

<footer class="site-footer">
  <div class="footer-cols">
    <div class="footer-brand"><span class="brand-dot"></span><span class="brand-name">Sunvale Energy</span></div>
    <div class="footer-col col-info">
      <h4>INFORMATION</h4>
      <p>August 14, 2017</p>
      <p>Sed ut perspiciatis unde omnis iste natus error sit voluptatem accusantium doloremque laudantium.</p>
    </div>
    <div class="footer-col col-contact">
      <h4>CONTACT US</h4>
      <ul>
        <li><svg width="12" height="12" viewBox="0 0 12 12"><path d="M2 1 L5 1 L6 4 L4.5 5 Q6 8 7 7.5 L8 6 L11 7 L11 10 Q6 12 2 6 Q0 3 2 1Z" fill="#fff"/></svg>(555) 014-7720 (Phone)</li>
        <li><svg width="12" height="12" viewBox="0 0 12 12"><path d="M2 1 L5 1 L6 4 L4.5 5 Q6 8 7 7.5 L8 6 L11 7 L11 10 Q6 12 2 6 Q0 3 2 1Z" fill="#fff"/></svg>(555) 014-7721 (Fax)</li>
        <li><svg width="12" height="10" viewBox="0 0 12 10"><rect x="0.5" y="0.5" width="11" height="9" fill="none" stroke="#fff"/><path d="M0.5 0.5 L6 5 L11.5 0.5" fill="none" stroke="#fff"/></svg>info@sunvaleenergy.com</li>
        <li><svg width="10" height="13" viewBox="0 0 10 13"><path d="M5 12 Q0 6 0 4.5 A5 5 0 0 1 10 4.5 Q10 6 5 12Z" fill="#fff"/><circle cx="5" cy="4.5" r="1.8" fill="#34a7d8"/></svg>12 Lorem Street, Sunvale</li>
      </ul>
    </div>
    <div class="footer-col col-news">
      <h4>NEWSLETTER</h4>
      <p>Register your email address to get information about us.</p>
      <div class="news-form"><span class="news-input">Email Address</span><span class="news-btn"></span></div>
    </div>
  </div>
  <div class="footer-bottom">
    <span>&copy; Copyright 2017 Sunvale Energy All Rights Reserved</span>
    <div class="social"><span></span><span></span><span></span><span></span><span></span><span></span></div>
  </div>
</footer>

</body>
</html>
```